Redesign current business card for food company

i would like to redesign my business card. our company is food company, our product range from chips, juices, milk and etc (mostly dried food stuff).
I want o keep same logo but , the rest is open to new design.
you can check at our website about our company www.orvelpantry.com

Target Market(s)

most of food company

Industry/Entity Type

Business

Contact Information for Business Card

I want to keep more to blue color...

Colors
3176b5
abd036

Requirements
Must have
• our old logo
Nice to have
• we do not mind to have nice material on bus card in order to accomplish nice design. for example: using spot uv, embossed and etc.

```html
<!DOCTYPE html>
<html lang="en">
<head>
<meta charset="utf-8">
<title>Orvel Pantry – Business Card</title>
<link href="https://fonts.googleapis.com/css2?family=Roboto:wght@300;400;500&display=swap" rel="stylesheet">
<style>
  :root {
    --brand-blue: #3176b5;
    --sky-blue: #3f9fd3;
    --deep-blue: #2a69a8;
    --leaf-green: #abd036;
    --ink-blue: #4a9fd6;
    --paper: #ffffff;
    --paper-shade: #eceeef;
    --stage: #e4e6e8;
  }
  * { margin: 0; padding: 0; box-sizing: border-box; }
  html, body { width: 1200px; height: 1023px; overflow: hidden; }
  body {
    background: var(--stage);
    font-family: "Roboto", sans-serif;
    position: relative;
  }
  .card {
    position: absolute;
    left: 320px;
    width: 560px;
    height: 320px;
    border-radius: 14px;
    overflow: hidden;
    box-shadow: 0 6px 18px rgba(0,0,0,.18);
  }
  .card--front { top: 140px; background: linear-gradient(135deg, var(--paper) 55%, var(--paper-shade)); }
  .card--back  { top: 563px; background: radial-gradient(circle at 50% 45%, var(--sky-blue), var(--deep-blue) 85%); }

  /* edge bands */
  .band { position: absolute; background: var(--leaf-green); }
  .card--front .band--top { left: 0; top: 0; width: 100%; height: 16px; }
  .card--front .band--top-accent { left: 0; top: 0; width: 150px; height: 16px; background: var(--brand-blue); }
  .card--front .band--bottom { left: 0; bottom: 0; width: 100%; height: 16px; }
  .card--front .band--left { left: 0; top: 0; width: 10px; height: 100%; }
  .card--front .band--right { right: 0; top: 0; width: 10px; height: 100%; }
  .card--front .corner-accent { position: absolute; right: 0; top: 46px; width: 16px; height: 40px; background: var(--brand-blue); }
  .card--back .band--left { left: 0; top: 0; width: 20px; height: 100%; }
  .card--back .band--right { right: 0; top: 0; width: 20px; height: 100%; }

  .brand-name {
    position: absolute;
    font-weight: 500;
    color: var(--brand-blue);
    letter-spacing: -1px;
    line-height: 1;
  }
  .card--front .brand-name { left: 48px; top: 74px; font-size: 64px; }
  .card--back .brand-name { left: 0; width: 100%; top: 108px; text-align: center; font-size: 110px; color: var(--paper); }

  .holder { position: absolute; right: 44px; top: 52px; text-align: right; }
  .holder__name { font-size: 24px; font-weight: 400; color: var(--ink-blue); }
  .holder__role { font-size: 13px; font-weight: 400; color: var(--leaf-green); margin-top: 2px; }

  .contact-list { position: absolute; list-style: none; }
  .contact-list--right { left: 310px; top: 138px; }
  .contact-list--left { left: 40px; top: 222px; }
  .contact-list li {
    display: flex; align-items: center; gap: 8px;
    font-size: 12.5px; font-weight: 300; color: var(--ink-blue);
    height: 22px;
  }
  .contact-icon { width: 16px; height: 16px; flex: none; }
  .contact-icon circle { fill: none; stroke: var(--leaf-green); stroke-width: 1.2; }
  .contact-icon .glyph { fill: none; stroke: var(--leaf-green); stroke-width: 1.2; stroke-linecap: round; stroke-linejoin: round; }
</style>
</head>
<body>

<section class="card card--front" aria-label="Business card front">
  <div class="band band--top"></div>
  <div class="band band--top-accent"></div>
  <div class="band band--left"></div>
  <div class="band band--right"></div>
  <div class="band band--bottom"></div>
  <div class="corner-accent"></div>

  <div class="brand-name">orvel</div>

  <div class="holder">
    <div class="holder__name">Marcus Delavente</div>
    <div class="holder__role">President</div>
  </div>

  <ul class="contact-list contact-list--right">
    <li><svg class="contact-icon" viewBox="0 0 16 16"><circle cx="8" cy="8" r="7.3"/><rect class="glyph" x="5.5" y="3.8" width="5" height="8.4" rx="1"/></svg>626 555 0193</li>
    <li><svg class="contact-icon" viewBox="0 0 16 16"><circle cx="8" cy="8" r="7.3"/><circle class="glyph" cx="8" cy="8" r="4"/><path class="glyph" d="M4 8h8M8 4c-2 2.5-2 5.5 0 8M8 4c2 2.5 2 5.5 0 8"/></svg>www.orvelpantry.com</li>
    <li><svg class="contact-icon" viewBox="0 0 16 16"><circle cx="8" cy="8" r="7.3"/><path class="glyph" d="M8 12.5s-3-3.2-3-5.3a3 3 0 0 1 6 0c0 2.1-3 5.3-3 5.3z"/><circle class="glyph" cx="8" cy="7.2" r="1"/></svg>2410 Alder Ave. Fairmont CA 91730</li>
  </ul>

  <ul class="contact-list contact-list--left">
    <li><svg class="contact-icon" viewBox="0 0 16 16"><circle cx="8" cy="8" r="7.3"/><path class="glyph" d="M5.2 4.5l1.6-.3.8 2-1 .8a5 5 0 0 0 2.4 2.4l.8-1 2 .8-.3 1.6c-3.5.3-6.6-2.8-6.3-6.3z"/></svg>909 555 0142</li>
    <li><svg class="contact-icon" viewBox="0 0 16 16"><circle cx="8" cy="8" r="7.3"/><rect class="glyph" x="4.2" y="6.5" width="7.6" height="5" rx=".6"/><path class="glyph" d="M5.8 6.5V4h4.4v2.5M6 9.5h4"/></svg>909 555 0178</li>
    <li><svg class="contact-icon" viewBox="0 0 16 16"><circle cx="8" cy="8" r="7.3"/><rect class="glyph" x="4" y="5" width="8" height="6" rx=".6"/><path class="glyph" d="M4 5.3l4 3 4-3"/></svg>marcus@orvelpantry.com</li>
  </ul>
</section>

<section class="card card--back" aria-label="Business card back">
  <div class="band band--left"></div>
  <div class="band band--right"></div>
  <div class="brand-name">orvel</div>
</section>

</body>
</html>
```